All natural lip balm label

Need a label design for a new all natural bath and body company (mytovabreel.com). We provide natural alternatives to harsh bath and body products. We have a lip balm that needs a new design!

I have attached my facebook cover photo because it might help with the design. But you do not have to use that.

Target Market(s)

people 30-55

Industry/Entity Type

It Company

Requirements
Must have
• Name of company is Tova Breel Bath & Body

must have "All Natural Lip Balm" near the logo

Must be in adobe illustrator EPS form (300 dpi) with 4 files (one for each flavor of lip balm: Herbal Mint, Cherry, Vanilla, Peppermint).
See details to art specs on my printer's site: http://www.quorvaprint.com/artspecs.htm (note that the text needs to be "outlined")

must be in the following size: 2.125000 x 2.125000 (2-1/8 x 2-1/8)

must have ingredients as shown below...
Ingredients: Organic Glycine Soja (soybean) Oil, Helianthus Annuus (sunflower) Seed Oil, Palm (Elaeis Guineensis) Oil, organic Olea Europaea (Olive) Fruit Oil, Avocado (Persea Gratissima) Oil, Beeswax (Cera Alba), Cocoa (Theobroma Cacao) Seed Butter, Shea Butter (Butyrospermum Parkii), Tocopherol Pure Vitamin E, Natural Flavor

Must have size of product on the label: "0.15 oz/4.25 g"

Must have following verbiage:
distributed by TovaBreel Bath & Body
Fernhollow, VT 53987
www.mytovabreel.com

must use the attached logo in some fashion (see "small logo" in attached files)
Nice to have
• use your imagination!

```html
<!DOCTYPE html>
<html lang="en">
<head>
<meta charset="utf-8">
<title>Tova Breel – All natural lip balm labels</title>
<link href="https://fonts.googleapis.com/css2?family=Ubuntu:ital,wght@0,400;0,500;0,700;1,400;1,500;1,700&display=swap" rel="stylesheet">
<style>
  :root {
    --page: #ffffff;
    --mint-accent: #2e7d32;
    --mint-soft: #9cc37a;
    --mint-ink: #3d4a32;
    --mint-brand: #5b6650;
    --cherry-accent: #b3174b;
    --cherry-soft: #f09ab4;
    --cherry-ink: #7a1836;
    --cherry-brand: #7a1836;
    --pepper-accent: #0f8a78;
    --pepper-soft: #7cc9bd;
    --pepper-ink: #0b4d45;
    --pepper-brand: #0b4d45;
    --vanilla-accent: #bcae68;
    --vanilla-soft: #e8de9a;
    --vanilla-ink: #8a7d45;
    --vanilla-brand: #8a7d45;
    --weight-text: #ffffff;
  }
  * { box-sizing: border-box; margin: 0; padding: 0; }
  html, body { width: 1200px; height: 1200px; overflow: hidden; background: var(--page); }
  body { position: relative; font-family: "Ubuntu", sans-serif; }

  .label {
    position: absolute;
    width: 553px; height: 553px;
    overflow: hidden;
    background: #fff;
    box-shadow: 0 1px 4px rgba(0,0,0,0.25);
    color: var(--ink);
  }
  .label--herbal-mint { left: 33px;  top: 37px;  --accent: var(--mint-accent);   --soft: var(--mint-soft);   --ink: var(--mint-ink);   --brand: var(--mint-brand); }
  .label--cherry      { left: 613px; top: 37px;  --accent: var(--cherry-accent); --soft: var(--cherry-soft); --ink: var(--cherry-ink); --brand: var(--cherry-brand); }
  .label--peppermint  { left: 33px;  top: 616px; --accent: var(--pepper-accent); --soft: var(--pepper-soft); --ink: var(--pepper-ink); --brand: var(--pepper-brand); }
  .label--vanilla     { left: 613px; top: 616px; --accent: var(--vanilla-accent); --soft: var(--vanilla-soft); --ink: var(--vanilla-ink); --brand: var(--vanilla-brand); }

  .label__swash {
    position: absolute; inset: 0;
    background:
      radial-gradient(ellipse 70% 30% at 85% 95%, var(--accent) 0%, transparent 70%),
      linear-gradient(160deg, color-mix(in srgb, var(--soft) 35%, #fff) 0%, #fff 35%, #fff 48%, color-mix(in srgb, var(--soft) 55%, #fff) 70%, var(--soft) 88%, var(--accent) 100%);
    opacity: 0.9;
  }

  .ingredients {
    position: absolute; left: 17px; top: 10px; width: 528px;
    font-size: 18.6px; line-height: 21.7px;
    color: var(--ink);
  }
  .ingredients__title { font-weight: 700; font-style: italic; color: var(--accent); }
  .label--herbal-mint .ingredients__title { color: var(--mint-ink); }
  .label--vanilla .ingredients { color: #7c7040; }

  .brand-mark {
    position: absolute; left: 33px; top: 236px;
    display: flex; align-items: center; gap: 12px;
    font-weight: 500; font-size: 50px; line-height: 60px; color: var(--accent);
    white-space: nowrap;
  }
  .brand-mark__dot {
    width: 44px; height: 44px; border-radius: 50%;
    background: var(--accent);
  }
  .tagline {
    position: absolute; left: 67px; top: 312px;
    font-size: 25px; line-height: 32px; font-weight: 700; color: var(--brand);
  }

  .flavor-icon {
    position: absolute; left: 383px; top: 258px;
    width: 70px; height: 42px; border-radius: 50%;
    background: linear-gradient(135deg, var(--accent), color-mix(in srgb, var(--accent) 70%, #fff));
  }
  .label--peppermint .flavor-icon { top: 238px; height: 76px; width: 74px; border-radius: 45%; }
  .label--cherry .flavor-icon { width: 46px; height: 46px; left: 393px; top: 256px; }
  .label--vanilla .flavor-icon { height: 18px; top: 272px; border-radius: 9px; background: linear-gradient(90deg, var(--soft), var(--accent)); }

  .flavor-name {
    position: absolute; left: 509px; top: 280px;
    transform: translate(-50%, -50%) rotate(-90deg);
    font-size: 17px; font-weight: 700; font-style: italic;
    color: var(--ink); white-space: nowrap;
  }
  .label--herbal-mint .flavor-name { color: var(--mint-brand); }
  .label--vanilla .flavor-name { color: var(--vanilla-accent); }

  .company {
    position: absolute; left: 17px; top: 404px;
    color: var(--brand); font-style: italic;
  }
  .company__name { font-size: 23.5px; font-weight: 700; line-height: 30px; }
  .company__line { font-size: 17.5px; line-height: 21.3px; }

  .net-weight {
    position: absolute; right: 29px; top: 492px;
    font-size: 31px; line-height: 38px; font-weight: 700; color: var(--weight-text);
    text-shadow: 0 0 6px rgba(0,0,0,0.12);
  }
</style>
</head>
<body>

<section class="label label--herbal-mint">
  <div class="label__swash" role="img" aria-label="Soft flowing green light swooshes"></div>
  <p class="ingredients"><span class="ingredients__title">Ingredients:</span> Organic Glycine Soja (soybean) Oil, Helianthus Annuus (sunflower) Seed Oil, Palm (Elaeis Guineensis) Oil, organic Olea Europaea (Olive) Fruit Oil, Avocado (Persea Gratissima) Oil, Beeswax (Cera Alba), Cocoa (Theobroma Cacao) Seed Butter, Shea Butter (Butyrospermum Parkii), Tocopherol Pure Vitamin E, Natural Flavor</p>
  <div class="brand-mark"><span>Tova</span><span class="brand-mark__dot"></span><span>Breel</span></div>
  <p class="tagline">All natural lip balm</p>
  <div class="flavor-icon" role="img" aria-label="Green mint leaf"></div>
  <p class="flavor-name">Herbal Mint</p>
  <div class="company">
    <p class="company__name">Tova Breel Bath &amp; Body</p>
    <p class="company__line">distributed by TovaBreel Bath &amp; Body</p>
    <p class="company__line">Fernhollow, VT 53987</p>
    <p class="company__line">www.mytovabreel.com</p>
  </div>
  <p class="net-weight">0.15 oz/4.25 g</p>
</section>

<section class="label label--cherry">
  <div class="label__swash" role="img" aria-label="Soft flowing pink and crimson light swooshes"></div>
  <p class="ingredients"><span class="ingredients__title">Ingredients:</span> Organic Glycine Soja (soybean) Oil, Helianthus Annuus (sunflower) Seed Oil, Palm (Elaeis Guineensis) Oil, organic Olea Europaea (Olive) Fruit Oil, Avocado (Persea Gratissima) Oil, Beeswax (Cera Alba), Cocoa (Theobroma Cacao) Seed Butter, Shea Butter (Butyrospermum Parkii), Tocopherol Pure Vitamin E, Natural Flavor</p>
  <div class="brand-mark"><span>Tova</span><span class="brand-mark__dot"></span><span>Breel</span></div>
  <p class="tagline">All natural lip balm</p>
  <div class="flavor-icon" role="img" aria-label="Red cherry"></div>
  <p class="flavor-name">Cherry</p>
  <div class="company">
    <p class="company__name">Tova Breel Bath &amp; Body</p>
    <p class="company__line">distributed by TovaBreel Bath &amp; Body</p>
    <p class="company__line">Fernhollow, VT 53987</p>
    <p class="company__line">www.mytovabreel.com</p>
  </div>
  <p class="net-weight">0.15 oz/4.25 g</p>
</section>

<section class="label label--peppermint">
  <div class="label__swash" role="img" aria-label="Soft flowing teal light swooshes"></div>
  <p class="ingredients"><span class="ingredients__title">Ingredients:</span> Organic Glycine Soja (soybean) Oil, Helianthus Annuus (sunflower) Seed Oil, Palm (Elaeis Guineensis) Oil, organic Olea Europaea (Olive) Fruit Oil, Avocado (Persea Gratissima) Oil, Beeswax (Cera Alba), Cocoa (Theobroma Cacao) Seed Butter, Shea Butter (Butyrospermum Parkii), Tocopherol Pure Vitamin E, Natural Flavor</p>
  <div class="brand-mark"><span>Tova</span><span class="brand-mark__dot"></span><span>Breel</span></div>
  <p class="tagline">All natural lip balm</p>
  <div class="flavor-icon" role="img" aria-label="Two peppermint leaves"></div>
  <p class="flavor-name">Peppermint</p>
  <div class="company">
    <p class="company__name">Tova Breel Bath &amp; Body</p>
    <p class="company__line">distributed by TovaBreel Bath &amp; Body</p>
    <p class="company__line">Fernhollow, VT 53987</p>
    <p class="company__line">www.mytovabreel.com</p>
  </div>
  <p class="net-weight">0.15 oz/4.25 g</p>
</section>

<section class="label label--vanilla">
  <div class="label__swash" role="img" aria-label="Soft flowing cream and gold light swooshes"></div>
  <p class="ingredients"><span class="ingredients__title">Ingredients:</span> Organic Glycine Soja (soybean) Oil, Helianthus Annuus (sunflower) Seed Oil, Palm (Elaeis Guineensis) Oil, organic Olea Europaea (Olive) Fruit Oil, Avocado (Persea Gratissima) Oil, Beeswax (Cera Alba), Cocoa (Theobroma Cacao) Seed Butter, Shea Butter (Butyrospermum Parkii), Tocopherol Pure Vitamin E, Natural Flavor</p>
  <div class="brand-mark"><span>Tova</span><span class="brand-mark__dot"></span><span>Breel</span></div>
  <p class="tagline">All natural lip balm</p>
  <div class="flavor-icon" role="img" aria-label="Vanilla pods"></div>
  <p class="flavor-name">Vanilla</p>
  <div class="company">
    <p class="company__name">Tova Breel Bath &amp; Body</p>
    <p class="company__line">distributed by TovaBreel Bath &amp; Body</p>
    <p class="company__line">Fernhollow, VT 53987</p>
    <p class="company__line">www.mytovabreel.com</p>
  </div>
  <p class="net-weight">0.15 oz/4.25 g</p>
</section>

</body>
</html>
```